Sleep/Snoring Business - Requires Website - Australia

We are seeking a simple to maintain website for our sleep business. The health care business provides diagnostic and treatment solutions for snoring, sleep disorders and other respiratory problems.

Ideally, colours to match the company logo (attached).

The page must be built using WORDPRESS.

Ideally site will have a home page outlining the business, with 5 sub pages - being "Diagnosis" "Treatment Options", "Prodcuts", "About Us", "Contact Us"

The site home page should include a large picture on the home page.

The "Treatment Options" and "Diagnosis" pages must include:
Allow for a few pictures with assocaited text, plus space for some embeded youtube videos.

"Prodcuts" page should have the ability to show 3-4 products across the page with text below.. that can include external URL to products

The "About Us" page must include:
1. a Map (google map) to identify the various locations. There are 6 in total.
2. A Section to describe our doctors/staff - allow for a picture and some text

The "Contact Us" page must include:
email form
telephone details

The overall design should have a clean and medical/safe feeling

Target Market(s)

People who snore and those with sleeping and respiratory disorders

Industry/Entity Type

Health Care

Coding

Coded - Design and coding required

Number of Pages Required

5+ page

Colors

Designer to choose colors to be used in the design.

Requirements
Must have
• The page must be built using WORDPRESS.
• Ideally site will have a home page outlining the business, with 5 sub pages - being "Diagnosis" "Treatment Options", "Prodcuts", "About Us", "Contact Us"
• The site home page should include a large picture on the home page.
• The "Treatment Options" and "Diagnosis" pages must include:
• Allow for a few pictures with assocaited text, plus space for some embeded youtube videos.
• "Prodcuts" page should have the ability to show 3-4 products across the page with text below.. that can include external URL to products
• The "About Us" page must include:
• 1. a Map (google map) to identify the various locations. There are 6 in total.
• 2. A Section to describe our doctors/staff - allow for a picture and some text
• The "Contact Us" page must include:
• email form
• telephone details
• Pictures must be licenced or free to use
Nice to have
• Home page pictures showing people sleeping well, snoring or fresh air (landscape) type transition pictures (at least 3).
Should not have
• Not to look cheap
• This is a high end healthcare business, so must look that way

```html
<!DOCTYPE html>
<html lang="en">
<head>
<meta charset="utf-8">
<title>Restwell Clinic – Home</title>
<link rel="stylesheet" href="https://fonts.googleapis.com/css2?family=Open+Sans:wght@400;600&family=Roboto:wght@400;500&display=swap">
<style>
:root{
  --navy:#0b3f7a;
  --ink:#222;
  --muted:#8a8a8a;
  --grey-bg:#f1f1f1;
  --news-bg:#f4f4f4;
  --footer:#121212;
  --footer-bar:#0a0a0a;
  --white:#fff;
}
*{margin:0;padding:0;box-sizing:border-box}
html,body{width:1200px;height:2616px;overflow:hidden}
body{position:relative;background:var(--white);font-family:"Open Sans",sans-serif;color:var(--ink)}
.heading{font-family:"Roboto",sans-serif;font-weight:400;text-transform:uppercase;color:var(--ink)}

/* header */
.site-header{position:absolute;left:0;top:0;width:1200px;height:122px;background:var(--white)}
.brand{position:absolute;left:87px;top:42px;font-family:"Roboto",sans-serif;font-size:30px;font-weight:500;color:var(--navy);white-space:nowrap}
.brand-footer{top:2404px;color:var(--white)}
.main-nav a{position:absolute;top:48px;height:31px;line-height:31px;text-align:center;font-size:14px;color:#222;text-decoration:none;white-space:nowrap;border-radius:16px}
.main-nav a.active{background:var(--navy);color:var(--white)}
.search-btn{position:absolute;left:1077px;top:48px}

/* hero */
.hero{position:absolute;left:0;top:122px;width:1200px;height:576px;background:linear-gradient(110deg,#e9edf2 0%,#f5f3f0 40%,#eef2f6 70%,#dfe8ef 100%)}
.hero-title{position:absolute;right:89px;top:388px;text-align:right;font-family:"Open Sans",sans-serif;font-size:45px;font-weight:600;color:var(--navy);white-space:nowrap}
.hero-sub{position:absolute;right:89px;top:444px;font-size:27px;color:#222;white-space:nowrap}
.hero-arrows{position:absolute;left:1053px;top:493px;display:flex;gap:6px}

/* diagnostic & treatment */
.grey-band{position:absolute;left:0;top:698px;width:1200px;height:352px;background:var(--grey-bg)}
.service-card{position:absolute;left:87px;top:614px;width:1026px;height:354px;background:var(--white);box-shadow:0 1px 6px rgba(0,0,0,.12)}
.service-card h2{position:absolute;top:44px;width:100%;text-align:center;font-size:24px}
.service{position:absolute;top:118px;width:280px;text-align:center}
.service svg{display:block;margin:0 auto}
.service h3{margin-top:14px;font-family:"Roboto",sans-serif;font-weight:400;font-size:17px;text-transform:uppercase;color:#222}
.service p{margin-top:14px;font-size:13px;line-height:19px;color:var(--muted)}
.service .more{display:block;margin-top:8px;font-size:13px;color:#222;text-decoration:none}

/* diagnostic techniques */
.video-still{position:absolute;left:0;top:1050px;width:576px;height:368px;background:linear-gradient(90deg,#e8ecef 0%,#d7dde2 45%,#6b6b6b 70%,#4a4a4a 100%)}
.play{position:absolute;left:253px;top:1200px}
.techniques{position:absolute;left:576px;top:1050px;width:624px;height:368px;background:var(--navy)}
.techniques h2{position:absolute;left:48px;top:66px;font-size:28px;color:var(--white)}
.techniques p{position:absolute;left:48px;top:108px;width:483px;font-size:14px;line-height:22px;color:var(--white);text-align:justify}
.btn-light{position:absolute;left:48px;top:282px;width:102px;height:30px;border-radius:15px;background:var(--white);color:#222;font-size:12px;line-height:30px;text-align:center;text-decoration:none}

/* treatment options */
.section-title{position:absolute;width:1200px;text-align:center;font-size:28px}
.section-sub{position:absolute;width:1200px;text-align:center;font-size:18px;color:#777}
.treat-card{position:absolute;top:1594px;width:240px;height:298px;background:var(--white);box-shadow:0 1px 5px rgba(0,0,0,.15);text-align:center}
.treat-photo{width:240px;height:167px}
.treat-card h3{margin-top:20px;font-family:"Roboto",sans-serif;font-weight:400;font-size:14px;text-transform:uppercase}
.treat-card p{margin:8px auto 0;width:210px;font-size:11.5px;line-height:17px;color:var(--muted)}
.btn-outline{display:inline-block;margin-top:10px;width:88px;height:23px;border:1px solid var(--navy);border-radius:12px;font-size:11px;line-height:21px;color:var(--navy);text-decoration:none}

/* news */
.news-band{position:absolute;left:0;top:1967px;width:1200px;height:347px;background:var(--news-bg)}
.news-item{position:absolute;top:2108px;width:480px;height:142px}
.news-photo{position:absolute;left:0;top:0;width:162px;height:142px}
.news-body{position:absolute;left:176px;top:8px;width:304px}
.news-body h3{font-size:14px;font-weight:400;color:#333}
.news-body time{display:block;margin-top:12px;font-size:12px;color:#333}
.news-body p{margin-top:6px;font-size:11.5px;line-height:18px;color:#444}
.news-body a{display:block;margin-top:6px;font-size:11.5px;color:var(--navy);text-decoration:none}

/* footer */
.site-footer{position:absolute;left:0;top:2314px;width:1200px;height:220px;background:var(--footer);color:var(--white)}
.footer-col{position:absolute;top:60px}
.footer-col h4{font-family:"Roboto",sans-serif;font-weight:500;font-size:13px;text-transform:uppercase;margin-bottom:18px}
.footer-col p{font-size:11.5px;line-height:21px}
.newsletter{display:flex;margin-top:10px}
.newsletter span{width:146px;height:30px;background:var(--white);color:#888;font-size:11px;line-height:30px;padding-left:8px}
.newsletter b{width:56px;height:30px;background:var(--navy);font-size:11.5px;font-weight:400;line-height:30px;text-align:center}
.social{display:flex;gap:15px;margin-top:2px}
.social i{display:block;width:24px;height:24px;background:var(--white);border-radius:3px}
.footer-bar{position:absolute;left:0;top:2534px;width:1200px;height:82px;background:var(--footer-bar);color:var(--white);text-align:center;font-size:13px;line-height:82px}
</style>
</head>
<body>

<header class="site-header">
  <div class="brand">Restwell Clinic</div>
  <nav class="main-nav">
    <a class="active" href="#" style="left:401px;width:80px">HOME</a>
    <a href="#" style="left:498px;width:100px">DIAGNOSIS</a>
    <a href="#" style="left:625px;width:170px">TREATMENT OPTIONS</a>
    <a href="#" style="left:823px;width:90px">ABOUT US</a>
    <a href="#" style="left:941px;width:110px">CONTACT US</a>
  </nav>
  <svg class="search-btn" width="32" height="32" viewBox="0 0 32 32" aria-label="Search">
    <circle cx="16" cy="16" r="15" fill="none" stroke="#0b3f7a" stroke-width="1.5"/>
    <circle cx="15" cy="15" r="4.5" fill="none" stroke="#0b3f7a" stroke-width="2"/>
    <line x1="18.3" y1="18.3" x2="21.5" y2="21.5" stroke="#0b3f7a" stroke-width="2.2" stroke-linecap="round"/>
  </svg>
</header>

<section class="hero" role="img" aria-label="Photo of a woman stretching happily in a bright white bedroom after waking up"></section>
<h1 class="hero-title">RESTWELL CLINIC</h1>
<p class="hero-sub">Neque porro quisquam dolorem</p>
<div class="hero-arrows">
  <svg width="26" height="26" viewBox="0 0 26 26"><circle cx="13" cy="13" r="13" fill="#8c8c8c"/><path d="M15 8l-5 5 5 5" fill="none" stroke="#fff" stroke-width="2"/></svg>
  <svg width="26" height="26" viewBox="0 0 26 26"><circle cx="13" cy="13" r="13" fill="#8c8c8c"/><path d="M11 8l5 5-5 5" fill="none" stroke="#fff" stroke-width="2"/></svg>
</div>

<div class="grey-band"></div>
<section class="service-card">
  <h2 class="heading">Diagnostic and Treatment</h2>
  <div class="service" style="left:57px">
    <svg width="64" height="64" viewBox="0 0 64 64" aria-hidden="true">
      <path d="M40 14a20 20 0 1 0 14 30A16 16 0 1 1 40 14z" fill="#0b3f7a"/>
      <text x="44" y="22" font-family="Roboto,sans-serif" font-size="14" font-weight="500" fill="#0b3f7a">z</text>
      <text x="52" y="12" font-family="Roboto,sans-serif" font-size="10" font-weight="500" fill="#0b3f7a">z</text>
    </svg>
    <h3>Snoring</h3>
    <p>It has survived not only five centuries, but also the leap into electronic typesetting.</p>
    <a class="more" href="#">Learn More -&gt;</a>
  </div>
  <div class="service" style="left:373px">
    <svg width="64" height="64" viewBox="0 0 64 64" aria-hidden="true">
      <circle cx="38" cy="16" r="11" fill="none" stroke="#0b3f7a" stroke-width="3"/>
      <path d="M38 10v6h5" fill="none" stroke="#0b3f7a" stroke-width="2.5"/>
      <rect x="6" y="34" width="4" height="24" fill="#0b3f7a"/>
      <rect x="6" y="44" width="52" height="8" rx="2" fill="#0b3f7a"/>
      <rect x="54" y="40" width="4" height="18" fill="#0b3f7a"/>
      <rect x="14" y="36" width="12" height="7" rx="3" fill="#0b3f7a"/>
    </svg>
    <h3>Sleep Disorders</h3>
    <p>It has survived not only five centuries, but also the leap into electronic typesetting.</p>
    <a class="more" href="#">Learn More -&gt;</a>
  </div>
  <div class="service" style="left:689px">
    <svg width="64" height="64" viewBox="0 0 64 64" aria-hidden="true">
      <path d="M32 8v20M32 28l-6 6M32 28l6 6" fill="none" stroke="#0b3f7a" stroke-width="3"/>
      <path d="M24 22c-10 0-16 16-16 28 0 6 4 8 8 6l10-5V26z" fill="#0b3f7a"/>
      <path d="M40 22c10 0 16 16 16 28 0 6-4 8-8 6l-10-5V26z" fill="#0b3f7a"/>
    </svg>
    <h3>Respiratory Problems</h3>
    <p>It has survived not only five centuries, but also the leap into electronic typesetting.</p>
    <a class="more" href="#">Learn More -&gt;</a>
  </div>
</section>

<div class="video-still" role="img" aria-label="Video still of a doctor in a white coat consulting with a patient"></div>
<svg class="play" width="62" height="62" viewBox="0 0 62 62" aria-label="Play video">
  <circle cx="31" cy="31" r="30" fill="#333" fill-opacity=".8"/>
  <path d="M25 19l18 12-18 12z" fill="#fff"/>
</svg>
<section class="techniques">
  <h2 class="heading" style="color:#fff">Diagnostic Techniques</h2>
  <p>It is a long established fact that a reader will be distracted by the readable content of a page when looking at its layout. The point of using Lorem Ipsum is that it has a more-or-less normal distribution of letters, as opposed to using 'Content here, content here', making it look like readable English. Many desktop publishing packages and web page editors now use Lorem Ipsum as their default model text, and a search for 'lorem ipsum' will uncover many web sites still in their infancy.</p>
  <a class="btn-light" href="#">Read More »</a>
</section>

<h2 class="section-title heading" style="top:1498px">Treatment Options</h2>
<p class="section-sub" style="top:1536px">Neque porro quisquam est qui dolorem</p>

<article class="treat-card" style="left:91px">
  <div class="treat-photo" role="img" aria-label="Photo of a couple in bed, one partner kept awake by snoring" style="background:linear-gradient(135deg,#e7e2dc,#c9c2bb)"></div>
  <h3>Snoring</h3>
  <p>It has survived not only five centuries, but also the leap into electronic</p>
  <a class="btn-outline" href="#">View More</a>
</article>
<article class="treat-card" style="left:349px">
  <div class="treat-photo" role="img" aria-label="Photo of a man lying awake in a dark bedroom at night" style="background:linear-gradient(135deg,#2d3a48,#5a6b7c)"></div>
  <h3>Sleep Disorders</h3>
  <p>It has survived not only five centuries, but also the leap into electronic</p>
  <a class="btn-outline" href="#">View More</a>
</article>
<article class="treat-card" style="left:607px">
  <div class="treat-photo" role="img" aria-label="Photo of an older man using an inhaler" style="background:linear-gradient(135deg,#d9d8d4,#a9a6a0)"></div>
  <h3>Respiratory Problems</h3>
  <p>It has survived not only five centuries, but also the leap into electronic</p>
  <a class="btn-outline" href="#">View More</a>
</article>
<article class="treat-card" style="left:867px">
  <div class="treat-photo" role="img" aria-label="Photo of a man asleep with an anti-snoring nasal strip" style="background:linear-gradient(135deg,#f1e6dc,#cdb8a6)"></div>
  <h3>Other Treatment</h3>
  <p>It has survived not only five centuries, but also the leap into electronic</p>
  <a class="btn-outline" href="#">View More</a>
</article>

<div class="news-band"></div>
<h2 class="section-title heading" style="top:2030px;font-size:26px">Latest News</h2>
<article class="news-item" style="left:91px">
  <div class="news-photo" role="img" aria-label="Photo of a doctor examining a chest X-ray" style="background:linear-gradient(135deg,#7d93a8,#c7d2dc)"></div>
  <div class="news-body">
    <h3>Nemo Enim Ipsam Volup</h3>
    <time>09-07-2017</time>
    <p>Lorem Ipsum has been the industry's standard dummy text ever since the 1500s, when an unknown printer took a galley of type and scrambled it to make a type specimen</p>
    <a href="#">Read More &gt;&gt;</a>
  </div>
</article>
<article class="news-item" style="left:630px;top:2100px">
  <div class="news-photo" role="img" aria-label="Photo of a doctor writing notes beside a stethoscope" style="background:linear-gradient(135deg,#3f6b9c,#c9d6e3)"></div>
  <div class="news-body">
    <h3>Nemo Enim Ipsam Volup</h3>
    <time>09-07-2017</time>
    <p>Lorem Ipsum has been the industry's standard dummy text ever since the 1500s, when an unknown printer took a galley of type and scrambled it to make a type specimen</p>
    <a href="#">Read More &gt;&gt;</a>
  </div>
</article>

<footer class="site-footer">
  <div class="footer-col" style="left:356px">
    <h4>Contact Us</h4>
    <p>Address : 12 Harbour Lane, Eastfield<br>NSW 2031<br>Phone : 02 5550 1842.<br>Email : hello@restwellclinic.example</p>
  </div>
  <div class="footer-col" style="left:656px">
    <h4>Sign Up for Newsletter</h4>
    <p style="width:210px;line-height:18px">Your about us information would fit here nicely.</p>
    <div class="newsletter"><span>Email address</span><b>Submit</b></div>
  </div>
  <div class="footer-col" style="left:949px">
    <h4>Follow Us Out There</h4>
    <div class="social"><i></i><i></i><i></i><i></i></div>
  </div>
</footer>
<div class="brand brand-footer">Restwell Clinic</div>
<div class="footer-bar">Copyright © 2017. All Rights Reserved</div>

</body>
</html>
```